Brightvale cleaning and maintenance company

An expansive website whereby we can advertise our commercial cleaning and maintenance services across a service portfolio of commercial cleaning and property maintenance. Whereby potential skilled resources can deposit there resume so we can collaborate and match candidates to a broad range of cleaning and maintenance jobs/projects.
Updates

Looking for more extensive ideas so the front page can change pictures on it with the focus for Brightvale Commercial Cleaning and Maintenance. Also need to bring in all the portfolios we offer including 1. Equipment Cleaning and Sanitisation Services 2. High pressure gurney and play ground equipment cleaning 3. General Cleaning and Property Facilities Management 4. Project and Recruiting Services, to allow for potential professional cleaners, handy man, mechanics, warehousing resources , electricians to deposit there resume. Most of the designers have stuck with the old portfolio categories , however the portfolio of services we offer has been updated so that needs to be reflected in the website. Also not necessary to use all my original photos I would like the opening page of the website to perhaps be able to change and have different pictures is that possible thank you

```html
<!DOCTYPE html>
<html lang="en">
<head>
<meta charset="utf-8">
<title>Brightvale – Commercial Cleaning &amp; Maintenance</title>
<link href="https://fonts.googleapis.com/css2?family=Noto+Serif:wght@400;700&family=Arimo:ital,wght@0,400;0,700;1,400&display=swap" rel="stylesheet">
<style>
:root{
  --orange:#f23c0b;
  --navy:#17306f;
  --navy-deep:#0f2a64;
  --pale:#eef1f7;
  --ink:#333a45;
  --white:#ffffff;
}
*{box-sizing:border-box;margin:0;padding:0}
html,body{width:1200px;height:4132px;overflow:hidden;background:var(--white)}
body{position:relative;font-family:"Arimo",Arial,sans-serif;color:var(--ink)}
.serif{font-family:"Noto Serif",Georgia,serif}
.abs{position:absolute}
.btn{position:absolute;background:var(--orange);color:var(--white);font-family:"Noto Serif",Georgia,serif;font-weight:700;font-size:15px;display:flex;align-items:center;justify-content:center;gap:7px;white-space:nowrap}
.btn .dot{width:9px;height:9px;border-radius:50%;background:var(--white)}

/* header */
.site-header{position:absolute;left:0;top:0;width:1200px;height:71px;background:var(--white);box-shadow:0 1px 4px rgba(0,0,0,.12);z-index:2}
.brand{position:absolute;left:173px;top:18px;display:flex;align-items:center;gap:8px;font-family:"Noto Serif",Georgia,serif;font-size:27px;color:var(--orange)}
.brand .mark{width:30px;height:30px;border-radius:50%;background:var(--navy)}
.main-nav{position:absolute;left:460px;top:28px;display:flex;gap:32px;font-family:"Noto Serif",Georgia,serif;font-size:13.5px;color:#444}
.main-nav .active{color:var(--orange)}

/* hero */
.hero{position:absolute;left:0;top:71px;width:1200px;height:592px;background:linear-gradient(100deg,#3c5e9a 0%,#5479b2 42%,#b9b8b6 43%,#d6d2cc 70%,#a9a7a3 100%)}
.hero-title{position:absolute;left:172px;top:188px;font-size:58px;font-weight:700;color:var(--white)}
.hero-sub{position:absolute;left:172px;top:262px;font-size:22px;font-weight:700;line-height:25px;color:var(--white)}
.hero-arrow{position:absolute;top:262px}
.contact-band{position:absolute;left:332px;top:630px;width:534px;height:65px}

/* sections */
.section-title{position:absolute;left:0;width:1200px;text-align:center;font-family:"Noto Serif",Georgia,serif;font-weight:700;font-size:56px;color:var(--navy)}
.service-card{position:absolute;width:555px;height:332px}
.service-label{position:absolute;left:24px;top:294px;width:485px;height:72px;display:flex;align-items:center;padding-left:24px;font-family:"Noto Serif",Georgia,serif;font-weight:700;font-size:22px;color:var(--white);background:var(--orange);clip-path:polygon(0 0,100% 0,96% 100%,0 100%);white-space:nowrap}

.careers-strip{position:absolute;left:173px;top:1612px;width:854px;height:50px;display:flex;align-items:center;justify-content:space-between;border:1px solid #d7dce8;padding:0 6px 0 20px}
.careers-strip p{font-size:13.5px;color:#3a3a3a}
.careers-strip strong{font-family:"Noto Serif",Georgia,serif;color:var(--navy);margin-right:8px}
.careers-strip .btn{position:static;width:190px;height:38px}

.about{position:absolute;left:0;top:1687px;width:1200px;height:528px;background:var(--pale)}
.about h2{position:absolute;left:173px;top:98px;font-size:56px;color:var(--navy)}
.about h3{position:absolute;left:173px;top:166px;font-size:19px;color:var(--orange);font-weight:700}
.about p{position:absolute;left:173px;top:208px;width:356px;font-size:12.8px;line-height:24.8px;color:#3a3a3a}
.about-photo{position:absolute;left:579px;top:92px;width:480px;height:345px;background:var(--white);padding:7px}
.about-photo div{width:100%;height:100%;background:linear-gradient(135deg,#9fd35a 0%,#6fa7b8 40%,#2a6f86 70%,#cfd8dc 100%)}

.gallery-intro{position:absolute;left:0;width:1200px;text-align:center;font-size:12.5px;line-height:24px;color:#444}
.tile{position:absolute}

.testimonials{position:absolute;left:0;top:2969px;width:1200px;height:484px;background:linear-gradient(180deg,#2a2e36,#1e2128)}
.testimonials h2{position:absolute;left:0;width:1200px;top:72px;text-align:center;font-size:42px;color:var(--white)}
.quote-card{position:absolute;top:172px;width:268px;height:200px;background:var(--white);padding:20px 14px}
.quote-card.featured{background:var(--orange)}
.quote-card .avatar{position:absolute;left:16px;top:18px;width:66px;height:66px;border-radius:50%;background:#c9b6a6}
.quote-card .name{position:absolute;left:95px;top:26px;font-family:"Noto Serif",Georgia,serif;font-weight:700;font-size:16px;color:var(--orange)}
.quote-card .text{position:absolute;left:95px;top:52px;width:160px;font-style:italic;font-size:12px;line-height:21px;color:#555}
.quote-card.featured .name,.quote-card.featured .text{color:var(--white)}

.client-name{position:absolute;top:3705px;width:190px;text-align:center;font-family:"Noto Serif",Georgia,serif;font-weight:700;font-size:20px;color:#2b2b2b;display:flex;align-items:center;justify-content:center;gap:8px}
.client-name .sq{width:12px;height:12px;background:#2b2b2b}
.slider-btn{position:absolute;top:3694px;width:56px;height:59px;background:#7d7d7d;display:flex;align-items:center;justify-content:center}

.site-footer{position:absolute;left:0;top:3847px;width:1200px;height:285px;background:var(--navy-deep);border-top:5px solid var(--orange)}
.footer-brand{position:absolute;left:0;width:1200px;top:50px;display:flex;justify-content:center;align-items:center;gap:10px;font-family:"Noto Serif",Georgia,serif;font-size:33px;color:var(--white)}
.footer-brand .mark{width:38px;height:38px;border-radius:50%;background:var(--white)}
.footer-nav{position:absolute;left:0;width:1200px;top:118px;text-align:center;font-family:"Noto Serif",Georgia,serif;font-size:16px;color:var(--white);word-spacing:2px}
.footer-nav span{margin:0 12px}
.footer-contact{position:absolute;left:0;width:1200px;top:174px;display:flex;justify-content:center;gap:28px;font-family:"Noto Serif",Georgia,serif;font-weight:700;font-size:20px;color:var(--white)}
.footer-contact a{color:var(--orange);text-decoration:underline}
.copyright{position:absolute;left:0;width:1200px;top:230px;text-align:center;font-size:12px;color:var(--white)}
</style>
</head>
<body>

<header class="site-header">
  <div class="brand"><span class="mark"></span>Brightvale</div>
  <nav class="main-nav">
    <span class="active">Home</span><span>Services</span><span>About Us</span><span>Our People</span><span>Safety &amp; Compliance</span><span>Contact</span>
  </nav>
</header>

<section class="hero" role="img" aria-label="Cleaner in uniform and yellow gloves vacuuming a living room sofa">
  <h1 class="hero-title serif">Brightvale</h1>
  <p class="hero-sub serif">A leading, Australian owned,<br>cleaning services company.</p>
  <div class="btn" style="left:172px;top:338px;width:128px;height:42px"><span class="dot"></span>Read More</div>
  <svg class="hero-arrow" style="left:34px" width="34" height="64" viewBox="0 0 34 64"><polyline points="30,2 4,32 30,62" fill="none" stroke="#fff" stroke-width="4"/></svg>
  <svg class="hero-arrow" style="left:1122px" width="34" height="64" viewBox="0 0 34 64"><polyline points="4,2 30,32 4,62" fill="none" stroke="#fff" stroke-width="4"/></svg>
</section>

<div class="contact-band">
  <svg width="534" height="65" viewBox="0 0 534 65" class="abs" style="left:0;top:0">
    <polygon points="0,32 22,0 512,0 534,32 512,65 22,65" fill="#fff"/>
    <polygon points="10,32 28,6 334,6 334,59 28,59" fill="#f23c0b"/>
    <polygon points="334,6 506,6 524,32 506,59 334,59" fill="#17306f"/>
    <path d="M48 22c2 0 4 5 4 6s-3 2-2 4 5 6 7 6 2-3 4-2 5 3 5 4-2 4-5 4c-6 0-16-10-16-17 0-3 2-5 3-5z" fill="#fff"/>
    <rect x="373" y="26" width="20" height="14" fill="none" stroke="#fff" stroke-width="2"/>
    <polyline points="373,26 383,34 393,26" fill="none" stroke="#fff" stroke-width="2"/>
  </svg>
  <span class="abs serif" style="left:70px;top:21px;color:#fff;font-weight:700;font-size:17px">Head office: (07) 5550 1284</span>
  <span class="abs serif" style="left:407px;top:22px;color:#fff;font-weight:700;font-size:15px">Contact Us</span>
</div>

<h2 class="section-title" style="top:722px">Our Services</h2>

<article class="service-card" style="left:29px;top:826px">
  <div style="width:555px;height:332px;background:linear-gradient(135deg,#7a6a5f,#d9d4cf 55%,#f5f3ef)" role="img" aria-label="Food service machine being cleaned and sanitised"></div>
  <div class="service-label">Equipment Cleaning &amp; Sanitisation</div>
</article>
<article class="service-card" style="left:614px;top:826px">
  <div style="width:555px;height:332px;background:linear-gradient(135deg,#c9a56a,#4a5fa0 50%,#e6d8d0)" role="img" aria-label="Children playing on clean playground equipment"></div>
  <div class="service-label">Gurney &amp; Playground Cleaning</div>
</article>
<article class="service-card" style="left:29px;top:1216px">
  <div style="width:555px;height:332px;background:linear-gradient(135deg,#3b2f22,#b9b3aa 50%,#6b6257)" role="img" aria-label="Cleaned commercial premises and facilities"></div>
  <div class="service-label">General Cleaning &amp; Facilities</div>
</article>
<article class="service-card" style="left:614px;top:1216px">
  <div style="width:555px;height:332px;background:linear-gradient(135deg,#7c7a76,#b7b5b0 50%,#8e8b85)" role="img" aria-label="Trades and maintenance team at work on site"></div>
  <div class="service-label">Project &amp; Recruiting Services</div>
</article>

<div class="careers-strip">
  <p><strong>Join our team</strong>Cleaners, handymen, mechanics, warehousing staff &amp; electricians welcome.</p>
  <div class="btn"><span class="dot"></span>Deposit Your Resume</div>
</div>

<section class="about">
  <h2 class="serif">About Us</h2>
  <h3 class="serif">Working with Brightvale</h3>
  <p>We are Brightvale, a leading, Australian owned, cleaning services company. When you work with Brightvale it is easy to do business with us. Our people are professional, reliable and service oriented. In every interaction you have; on site, receiving help from our service support staff, or rolling-out new cleaning sites, you will see and feel the benefits of using Brightvale.</p>
  <div class="btn" style="left:172px;top:393px;width:128px;height:42px"><span class="dot"></span>Read More</div>
  <div class="about-photo"><div role="img" aria-label="Gloved hands spraying and wiping a table beside a green bucket"></div></div>
</section>

<h2 class="section-title" style="top:2270px">Our Gallery</h2>
<p class="gallery-intro" style="top:2343px">Lorem ipsum dolor sit amet, consectetur adipiscing elit, sed do eiusmod tempor incididunt<br>et dolore magna aliquenim ad minim veniam, quis nostrud exercitation ullamoris.</p>

<div class="tile" style="left:173px;top:2427px;width:419px;height:224px;background:linear-gradient(135deg,#8a8576,#d8d2bd 50%,#6a6457)" role="img" aria-label="Disassembled machine parts on a bench"></div>
<div class="tile" style="left:600px;top:2427px;width:210px;height:149px;background:linear-gradient(135deg,#eceff1,#c9cfd4 60%,#d889b2)" role="img" aria-label="Cleaner wiping a bathroom sink"></div>
<div class="tile" style="left:818px;top:2427px;width:209px;height:149px;background:linear-gradient(135deg,#4f6b3a,#8a5a3e 60%,#5c4332)" role="img" aria-label="Pressure cleaning a timber deck"></div>
<div class="tile" style="left:173px;top:2659px;width:209px;height:150px;background:linear-gradient(135deg,#3b3a39,#9aa3a8 55%,#2c5fa8)" role="img" aria-label="Hosing down kitchen equipment"></div>
<div class="tile" style="left:390px;top:2659px;width:202px;height:150px;background:linear-gradient(135deg,#f2f2f0,#d8d4cc 60%,#a89a8a)" role="img" aria-label="Cleaner mopping a bright room"></div>
<div class="tile" style="left:600px;top:2584px;width:427px;height:225px;background:linear-gradient(135deg,#8c8c8c,#cfc6b6 55%,#6e6e6e)" role="img" aria-label="Close-up of a machine dispensing fitting"></div>

<div class="btn" style="left:536px;top:2849px;width:128px;height:41px"><span class="dot"></span>View More</div>

<section class="testimonials" role="img" aria-label="Dark background of carpet being cleaned">
  <h2 class="serif">Testimonials</h2>
  <div class="quote-card" style="left:175px">
    <div class="avatar"></div><div class="name">Marcus</div>
    <div class="text">"Lorem ipsum dolor sit met conse ctetur adipiscing elie do iusmod tempm ipsumdo lor sit amet, consectetulorr adipl oorem ipsumdo lsec teturlore adipisdo"</div>
  </div>
  <div class="quote-card featured" style="left:465px">
    <div class="avatar"></div><div class="name">Jolene</div>
    <div class="text">"Lorem ipsum dolor sit met conse ctetur adipiscing elie do iusmod tempm ipsumdo lor sit amet, consectetulorr adipl oorem ipsumdo lsec teturlore adipisdo"</div>
  </div>
  <div class="quote-card" style="left:757px">
    <div class="avatar"></div><div class="name">Bree Lawson</div>
    <div class="text">"Lorem ipsum dolor sit met conse ctetur adipiscing elie do iusmod tempm ipsumdo lor sit amet, consectetulorr adipl oorem ipsumdo lsec teturlore adipisdo"</div>
  </div>
</section>

<h2 class="section-title" style="top:3488px">Clients</h2>
<p class="gallery-intro" style="top:3559px">This reputation is reflected in the organisations that have trusted us to<br>support them both locally and nationally, including:</p>

<div class="slider-btn" style="left:114px"><svg width="30" height="16" viewBox="0 0 30 16"><path d="M29 8H2M9 1 2 8l7 7" fill="none" stroke="#fff" stroke-width="2"/></svg></div>
<div class="client-name" style="left:205px"><span class="sq"></span>Ridgeway Grill</div>
<div class="client-name" style="left:405px">Harbor Diner</div>
<div class="client-name" style="left:620px">Summit Beverages</div>
<div class="client-name" style="left:835px">Copper Kettle</div>
<div class="slider-btn" style="left:1028px"><svg width="30" height="16" viewBox="0 0 30 16"><path d="M1 8h27M21 1l7 7-7 7" fill="none" stroke="#fff" stroke-width="2"/></svg></div>

<footer class="site-footer">
  <div class="footer-brand"><span class="mark"></span>Brightvale</div>
  <nav class="footer-nav">Home<span>|</span>Services<span>|</span>About Us<span>|</span>Our People<span>|</span>Safety &amp; Compliance<span>|</span>Contact</nav>
  <div class="footer-contact">
    <span style="display:flex;align-items:center;gap:10px"><svg width="20" height="22" viewBox="0 0 20 22"><path d="M4 1c2 0 4 5 4 6s-3 2-2 4 5 6 7 6 2-3 4-2 3 3 3 4-2 3-5 3C8 22 0 13 0 6c0-3 2-5 4-5z" fill="#fff"/></svg>Head office: (07) 5550 1284</span>
    <span style="display:flex;align-items:center;gap:10px"><svg width="24" height="16" viewBox="0 0 24 16"><rect x="1" y="1" width="22" height="14" fill="none" stroke="#fff" stroke-width="2"/><polyline points="1,1 12,9 23,1" fill="none" stroke="#fff" stroke-width="2"/></svg><a>Email us</a></span>
  </div>
  <p class="copyright">Copyright 2020 Brightvale.com. All right reserved.</p>
</footer>

</body>
</html>
```